Pine Ledge Traders, LLC- Global Beverage Company with 100% Cold Chain Logistics

Hey All, My Name is Dale, I am a young business owner in a competitive export space, but my niche is that I am shipping all of my beer around the world, "100% Cold Chain". This model is more costly, but it protects the integrity of the beer itself and will give folks in foreign countries the best representation of what US Craft Beer has to offer.

I am not a branding guy and don't claim to be one, I am a salesperson first, and will be referring to all of you to create something great that will be memorable.

I am looking for a basic Business Card Design for my Craft Beer Export company. I sell US Craft Beer in several countries around the globe. Austrailia, China, Taiwan, Chile, France, New Zealand... to name a few.

I am looking for a sleek, modern, and fresh design. Quickly!

Thanks for your consideration!

Cheers,

Dale

Target Market(s)

International

Contact Information for Business Card

Dale Corrigan
Founder- Roaming Hops Guy
Dale@PineLedgeTraders.example
@RoamingHopsGuy- Instagram only
www.Pineledgetraders.example
@PineLedgeTradersAU- Instagram Only

Font styles to use
Serif

Colors
0592cd
ffffff

Requirements
Must have
• Name-
• Title-
• Email-
• Social Media Handle-
• Company Website-
Nice to have
• Nice Logo/ Images on Card
Should not have
• Tacky Beer Images

```html
<!DOCTYPE html>
<html lang="en">
<head>
<meta charset="utf-8">
<title>Roaming Hops Guy – Business Card</title>
<link rel="stylesheet" href="https://fonts.googleapis.com/css2?family=Barlow+Semi+Condensed:wght@400;600;700&display=swap">
<style>
  :root {
    --brand-blue: #0592cd;
    --light-blue: #8fd0ec;
    --mid-blue: #4fb3e0;
    --white: #ffffff;
    --board-grey: #c7c8ca;
    --rule-grey: #c9ccd0;
    --shadow: rgba(0, 0, 0, 0.22);
  }
  * { box-sizing: border-box; margin: 0; padding: 0; }
  html, body { width: 1200px; height: 706px; overflow: hidden; }
  body {
    position: relative;
    background: var(--board-grey);
    font-family: "Barlow Semi Condensed", Arial, sans-serif;
  }
  .side-label {
    position: absolute;
    left: 271px;
    font-size: 28px;
    font-weight: 700;
    color: var(--brand-blue);
    letter-spacing: 0.5px;
  }
  .side-label--back { top: 146px; }
  .side-label--front { top: 494px; }

  .card {
    position: absolute;
    left: 379px;
    width: 443px;
    height: 281px;
    background: var(--white);
    overflow: hidden;
    box-shadow: 0 14px 18px -8px var(--shadow);
  }
  .card--back { top: 37px; }
  .card--front { top: 356px; }

  .stripe { position: absolute; display: block; }
  .stripe--left { left: 0; top: 151px; }
  .stripe--right { right: 0; top: 207px; }

  .mark-art {
    position: absolute;
    border-radius: 50%;
    background: radial-gradient(circle, rgba(5,146,205,0.35) 0%, rgba(5,146,205,0.12) 55%, rgba(5,146,205,0) 72%);
  }
  .card--back .mark-art { left: 140px; top: 22px; width: 150px; height: 150px; }

  .brand-name {
    position: absolute;
    left: 135px;
    width: 160px;
    top: 188px;
    text-align: center;
    font-size: 24px;
    line-height: 1.0;
    font-weight: 700;
    color: var(--brand-blue);
  }
  .brand-name span { display: block; }

  .front-top-band {
    position: absolute; left: 0; top: 0; width: 100%; height: 7px;
    background: var(--brand-blue);
  }
  .front-shade {
    position: absolute; left: 0; top: 7px; width: 100%; height: 137px;
  }
  .front-rule {
    position: absolute; left: 210px; top: 135px; width: 233px;
    border-top: 1px dashed var(--rule-grey);
  }
  .front-panel {
    position: absolute; left: 0; top: 144px; width: 100%; height: 137px;
    background: var(--brand-blue);
  }
  .card--front .mark-art {
    left: 240px; top: 30px; width: 200px; height: 200px;
    background: radial-gradient(circle, rgba(255,255,255,0.95) 0%, rgba(200,230,245,0.75) 40%, rgba(5,146,205,0) 70%);
  }

  .person { position: absolute; left: 30px; top: 58px; }
  .person__name {
    font-size: 18px; font-weight: 700; color: var(--brand-blue); line-height: 1.1;
  }
  .person__title {
    font-size: 13px; font-weight: 400; color: var(--brand-blue); margin-top: 2px;
  }

  .contacts {
    position: absolute; left: 30px; top: 172px; list-style: none;
  }
  .contacts__item {
    display: flex; align-items: center; gap: 8px;
    height: 22.5px;
    font-size: 13px; color: var(--white);
  }
  .contacts__icon {
    width: 19px; height: 19px; border-radius: 50%;
    background: var(--white);
    display: flex; align-items: center; justify-content: center;
    flex: none;
  }
</style>
</head>
<body>
  <div class="side-label side-label--back">BACK</div>
  <div class="side-label side-label--front">FRONT</div>

  <section class="card card--back">
    <svg class="stripe stripe--left" width="120" height="8" viewBox="0 0 120 8">
      <polygon points="0,0 40,0 44,8 0,8" fill="var(--light-blue)"/>
      <polygon points="44,0 72,0 76,8 48,8" fill="var(--mid-blue)"/>
      <polygon points="76,0 110,0 118,8 80,8" fill="var(--brand-blue)"/>
    </svg>
    <div class="mark-art" role="img" aria-label="Line illustration of a frothy beer mug with radiating rays"></div>
    <div class="brand-name"><span>Roaming</span><span>Hops Guy</span></div>
    <svg class="stripe stripe--right" width="137" height="9" viewBox="0 0 137 9">
      <polygon points="0,0 22,0 30,9 8,9" fill="var(--light-blue)"/>
      <polygon points="24,0 44,0 52,9 32,9" fill="var(--mid-blue)"/>
      <polygon points="46,0 137,0 137,9 54,9" fill="var(--brand-blue)"/>
    </svg>
  </section>

  <section class="card card--front">
    <div class="front-top-band"></div>
    <svg class="front-shade" viewBox="0 0 443 137" preserveAspectRatio="none">
      <defs>
        <linearGradient id="shadeFill" x1="0" y1="0" x2="1" y2="0">
          <stop offset="0" stop-color="#f4f5f6"/>
          <stop offset="1" stop-color="#e3e5e8"/>
        </linearGradient>
      </defs>
      <polygon points="170,0 443,0 443,137 250,137" fill="url(#shadeFill)"/>
    </svg>
    <div class="front-rule"></div>
    <div class="front-panel"></div>
    <div class="mark-art" role="img" aria-label="Line illustration of a frothy beer mug with radiating rays"></div>

    <div class="person">
      <div class="person__name">Dale Corrigan</div>
      <div class="person__title">Founder-Roaming Hops Guy</div>
    </div>

    <ul class="contacts">
      <li class="contacts__item">
        <span class="contacts__icon">
          <svg width="11" height="11" viewBox="0 0 24 24"><path fill="var(--brand-blue)" d="M6.6 10.8a15.1 15.1 0 0 0 6.6 6.6l2.2-2.2a1 1 0 0 1 1-.25 11.4 11.4 0 0 0 3.6.57 1 1 0 0 1 1 1V20a1 1 0 0 1-1 1A17 17 0 0 1 3 4a1 1 0 0 1 1-1h3.5a1 1 0 0 1 1 1c0 1.250.2 2.450.57 3.570a1 1 0 0 1-.25 1z"/></svg>
        </span>
        Business Telephone
      </li>
      <li class="contacts__item">
        <span class="contacts__icon">
          <svg width="12" height="12" viewBox="0 0 24 24"><circle cx="12" cy="12" r="4" fill="none" stroke="var(--brand-blue)" stroke-width="2.4"/><path d="M16 8v5.5a2.5 2.5 0 0 0 5 0V12a9 9 0 1 0-3.5 7.1" fill="none" stroke="var(--brand-blue)" stroke-width="2.4"/></svg>
        </span>
        Dale@PineLedgeTraders.example
      </li>
      <li class="contacts__item">
        <span class="contacts__icon">
          <svg width="8" height="8" viewBox="0 0 10 10"><circle cx="5" cy="5" r="4" fill="var(--brand-blue)"/></svg>
        </span>
        @RoamingHopsGuy
      </li>
      <li class="contacts__item">
        <span class="contacts__icon">
          <svg width="12" height="12" viewBox="0 0 24 24" fill="none" stroke="var(--brand-blue)" stroke-width="2"><circle cx="12" cy="12" r="9"/><ellipse cx="12" cy="12" rx="4" ry="9"/><path d="M3 12h18M5 7h14M5 17h14"/></svg>
        </span>
        www.Pineledgetraders.example
      </li>
    </ul>
  </section>
</body>
</html>
```